BOLD & MINIMALIST DESIGN NEEDED

We want a very bold but minimalistic business card design that is impactful and utilizes both sides of the business card. Our current logo is included for your use.

We want bold fonts and good use of negative space. We don't want the logo to overpower the design.

Target Market(s)

Professionals who are building new commercial buildings.

Industry/Entity Type

Construction

Contact Information for Business Card

Name, Title, email, office phone, cell phone, website

Font styles to use
Serif
Sans Serif

Requirements
Must have
• Bold design!

```html
<!DOCTYPE html>
<html lang="en">
<head>
<meta charset="utf-8">
<title>Ridgeline Business Card</title>
<link rel="stylesheet" href="https://fonts.googleapis.com/css2?family=Open+Sans:wght@300;400;700;800&display=swap">
<style>
  :root {
    --backdrop: #9a9a9a;
    --card-dark: #1d1d1d;
    --card-light: #f4f4f2;
    --accent: #86c03f;
    --ink: #1f1f1f;
    --white: #ffffff;
    --muted: #e6e6e6;
  }
  * { box-sizing: border-box; margin: 0; padding: 0; }
  html, body {
    width: 1200px;
    height: 1019px;
    overflow: hidden;
  }
  body {
    background: linear-gradient(135deg, #bdbdbd 0%, var(--backdrop) 50%, #7a7a7a 100%);
    font-family: "Open Sans", Arial, sans-serif;
    position: relative;
  }
  .card {
    position: absolute;
    left: 250px;
    width: 700px;
    height: 400px;
    border-radius: 32px;
    overflow: hidden;
    box-shadow: 0 14px 30px rgba(0,0,0,0.25);
  }

  /* Back side */
  .card--back {
    top: 80px;
    background: var(--card-dark);
    color: var(--white);
  }
  .identity {
    position: absolute;
    left: 44px;
    top: 42px;
    padding-left: 20px;
    border-left: 7px solid var(--accent);
  }
  .identity__name {
    font-weight: 800;
    font-size: 30px;
    letter-spacing: -0.5px;
    line-height: 1.1;
    text-transform: uppercase;
  }
  .identity__title {
    font-weight: 300;
    font-size: 24px;
    color: var(--muted);
    line-height: 1.2;
  }
  .brand-mark {
    position: absolute;
    right: 76px;
    top: 172px;
    display: flex;
    align-items: center;
    gap: 10px;
    font-weight: 800;
    font-size: 26px;
    letter-spacing: 1px;
    text-transform: uppercase;
    color: var(--white);
  }
  .brand-mark__dot {
    width: 14px;
    height: 14px;
    background: var(--accent);
    border-radius: 50%;
  }
  .contact {
    position: absolute;
    right: 44px;
    bottom: 40px;
    list-style: none;
    text-align: right;
  }
  .contact__item {
    display: flex;
    justify-content: flex-end;
    align-items: center;
    gap: 14px;
    font-size: 19px;
    line-height: 1.5;
    color: var(--white);
  }
  .contact__icon {
    width: 18px;
    height: 18px;
    fill: var(--accent);
    flex: none;
  }

  /* Front side */
  .card--front {
    top: 540px;
    background: var(--card-light);
  }
  .brand-name {
    position: absolute;
    left: 0;
    right: 0;
    top: 150px;
    display: flex;
    justify-content: center;
    align-items: center;
    gap: 14px;
    font-weight: 800;
    font-size: 50px;
    letter-spacing: 1px;
    text-transform: uppercase;
    color: var(--ink);
  }
  .brand-name__square {
    width: 22px;
    height: 22px;
    background: var(--accent);
  }
  .web-band {
    position: absolute;
    left: 0;
    right: 0;
    top: 262px;
    height: 48px;
    background: var(--accent);
    display: flex;
    align-items: center;
    justify-content: center;
    font-weight: 700;
    font-size: 22px;
    letter-spacing: 5px;
    color: var(--ink);
  }
</style>
</head>
<body>

  <section class="card card--back" aria-label="Card back">
    <div class="identity">
      <p class="identity__name">Daniel Reeves</p>
      <p class="identity__title">Manager</p>
    </div>

    <div class="brand-mark">
      <span class="brand-mark__dot"></span>
      <span>Ridgeline</span>
    </div>

    <ul class="contact">
      <li class="contact__item">
        <span>041-735-2200</span>
        <svg class="contact__icon" viewBox="0 0 24 24" aria-hidden="true"><path d="M6.6 10.8a15.1 15.1 0 0 0 6.6 6.6l2.2-2.2c.3-.3.7-.4 1-.2 1.1.4 2.3.6 3.6.6.6 0 1 .4 1 1V20c0 .6-.4 1-1 1A17 17 0 0 1 3 4c0-.6.4-1 1-1h3.5c.6 0 1 .4 1 1 0 1.3.2 2.5.6 3.6.1.3 0 .7-.2 1z"/></svg>
      </li>
      <li class="contact__item">
        <span>+5718 3364 902</span>
        <svg class="contact__icon" viewBox="0 0 24 24" aria-hidden="true"><path d="M4 3h5v18H4zM11 6h9v15h-9zm2 3v3h5V9zm0 5v2h2v-2zm3 0v2h2v-2zm-3 3v2h2v-2zm3 0v2h2v-2z"/></svg>
      </li>
      <li class="contact__item">
        <span>daniel@ridgelinebuild.com</span>
        <svg class="contact__icon" viewBox="0 0 24 24" aria-hidden="true"><path d="M2 5h20v14H2zm2 2v.4l8 5.2 8-5.2V7zm0 2.8V17h16V9.8l-8 5.2z"/></svg>
      </li>
    </ul>
  </section>

  <section class="card card--front" aria-label="Card front">
    <div class="brand-name">
      <span class="brand-name__square"></span>
      <span>Ridgeline</span>
    </div>
    <div class="web-band">www.ridgelinebuild.com</div>
  </section>

</body>
</html>
```